Corvel Capital LLC

Need Professional Business cards for New Investment Fund

Target Market(s)

High Quality investors

Industry/Entity Type

Financial

Contact Information for Business Card

Phone Number +1 555 284 6190
Name Lukas Varenko
Title Fund Manager
email lv@FundCorvel.com
Website www.FundCorvel.com

Colors

Designer to choose colors to be used in the design.

Requirements
Must have
• Must have our Logo and all of the above. Must be made so lettering and loge can be raised

```html
<!DOCTYPE html>
<html lang="en">
<head>
<meta charset="utf-8">
<title>Orvanel Fund — Business Card</title>
<link rel="stylesheet" href="https://fonts.googleapis.com/css2?family=Roboto:wght@400;500;700&display=swap">
<style>
  :root {
    --bg: #1f2020;
    --slate: #434d43;
    --green: #22e400;
    --white: #ffffff;
    --card-w: 700px;
    --card-h: 400px;
  }
  * { box-sizing: border-box; margin: 0; padding: 0; }
  html, body {
    width: 1200px; height: 960px; overflow: hidden;
    background: var(--bg);
    font-family: "Roboto", Arial, sans-serif;
  }
  .stage { position: relative; width: 1200px; height: 960px; }
  .card {
    position: absolute; left: 250px;
    width: var(--card-w); height: var(--card-h);
    overflow: hidden;
  }
  .card--back { top: 50px; background: var(--slate); }
  .card--front { top: 500px; background: var(--white); }

  /* Back */
  .back-brand {
    position: absolute; left: 0; right: 0; top: 150px;
    display: flex; align-items: center; justify-content: center; gap: 14px;
  }
  .brand-mark { width: 26px; height: 26px; background: var(--white); flex: none; }
  .back-brand .brand-name {
    color: var(--white); font-weight: 500; font-size: 44px; letter-spacing: 4px; line-height: 1;
  }
  .back-web {
    position: absolute; left: 0; right: 0; top: 236px;
    text-align: center; color: var(--white); font-size: 17px; letter-spacing: 2px;
  }

  /* Front */
  .card-shapes { position: absolute; inset: 0; }
  .front-brand {
    position: absolute; right: 60px; top: 72px;
    display: flex; align-items: center; gap: 12px;
  }
  .front-brand .brand-mark { width: 22px; height: 22px; background: var(--green); }
  .front-brand .brand-name {
    color: var(--slate); font-weight: 500; font-size: 36px; letter-spacing: 3px; line-height: 1;
  }
  .person { position: absolute; right: 40px; top: 272px; text-align: right; }
  .person-name { color: var(--green); font-weight: 700; font-size: 27px; line-height: 1.2; }
  .person-title { color: var(--white); font-weight: 500; font-size: 17px; margin-top: 2px; }
  .contacts { position: absolute; left: 50px; top: 304px; list-style: none; }
  .contact {
    display: flex; align-items: center; gap: 12px;
    color: var(--white); font-size: 17px; line-height: 27px;
  }
  .contact svg { width: 15px; height: 15px; flex: none; }
</style>
</head>
<body>
<main class="stage">

  <section class="card card--back" aria-label="Card back">
    <div class="back-brand">
      <span class="brand-mark"></span>
      <span class="brand-name">ORVANEL</span>
    </div>
    <p class="back-web">www.FundCorvel.com</p>
  </section>

  <section class="card card--front" aria-label="Card front">
    <svg class="card-shapes" viewBox="0 0 700 400" width="700" height="400" aria-hidden="true">
      <polygon points="0,280 310,280 440,400 0,400" fill="var(--green)"/>
      <polygon points="300,255 700,255 700,400 458,400" fill="var(--slate)"/>
    </svg>

    <div class="front-brand">
      <span class="brand-mark"></span>
      <span class="brand-name">ORVANEL</span>
    </div>

    <div class="person">
      <p class="person-name">Lukas Varenko</p>
      <p class="person-title">Fund Manager</p>
    </div>

    <ul class="contacts">
      <li class="contact">
        <svg viewBox="0 0 16 16"><path fill="#fff" d="M3.6 1.2l2.3 2.6-1.3 1.9c.9 2 2.5 3.6 4.6 4.6l1.9-1.3 2.6 2.3-1.4 2.4C7 13.3 2.7 9 1.2 3z"/></svg>
        <span>+1 555 284 6190</span>
      </li>
      <li class="contact">
        <svg viewBox="0 0 16 16"><rect x="1" y="3" width="14" height="10" fill="#fff"/><path d="M1.5 3.5L8 9l6.5-5.5" stroke="var(--green)" stroke-width="1.4" fill="none"/></svg>
        <span>lv@FundCorvel.com</span>
      </li>
      <li class="contact">
        <svg viewBox="0 0 16 16"><circle cx="8" cy="8" r="7" fill="#fff"/><path d="M4 5c2 0 2 2 4 2s1 3-1 3-1 3-3 2M10 3c0 2 2 2 3 3" stroke="var(--green)" stroke-width="1.3" fill="none"/></svg>
        <span>www.FundCorvel.com</span>
      </li>
    </ul>
  </section>

</main>
</body>
</html>
```